Refresh of far from plain IT company website

Our web site is starting to show it's age. You can see the existing site here: www.plumbwick.net. As a growing company we want to come across as a dynamic collection of IT experts.

We want to update the design so are open to any colour palette and look, but want to retain our current table logo. We use the logo on our business cards but with a white background - see the attached file, so you don't need to keep the brown or the green.

The design should consider the range of browsers that will be looking at the site - so please show how it will look on a wide screen laptop and a 768x1024 tablet.

We want to add some pages about our team and their skills, probably with photos of each person on the team.

This is an uncoded project - the PSD files of the design is required, not coding.
Updates

Thanks everyone for the submissions so far.  It's a holiday day in the UK today but we will get some feedback on the designs so far out to you.

Target Market(s)

Architects and other creative types looking for IT support

Industry/Entity Type

Business

Font styles to use
Serif
Sans Serif

Requirements
Must have
• Must look good on a laptop and an iPad.

```html
<!DOCTYPE html>
<html lang="en">
<head>
<meta charset="utf-8">
<title>Plumbwick – IT Support &amp; Management</title>
<link href="https://fonts.googleapis.com/css2?family=Arimo:wght@400;700&display=swap" rel="stylesheet">
<style>
:root{
  --brand:#9c0d57;
  --gold:#d7b00f;
  --ink:#333;
  --muted:#555;
  --light:#eeeeee;
  --footer:#454545;
  --hero:#000;
  --line:#dcdcdc;
}
*{margin:0;padding:0;box-sizing:border-box}
html,body{width:1089px;height:1200px;overflow:hidden;background:#fff}
body{font-family:"Arimo",Arial,sans-serif;color:var(--ink);position:relative}
.abs{position:absolute}
a{color:inherit;text-decoration:none}

/* header */
.site-header{position:absolute;left:0;top:0;width:1089px;height:56px;background:#fff}
.brand{position:absolute;left:158px;top:13px;display:flex;align-items:center;gap:12px}
.brand-mark{width:24px;height:22px;background:var(--gold)}
.brand-name{font-size:27px;color:var(--brand);font-weight:400;letter-spacing:.2px}
.main-nav a{position:absolute;top:22px;font-size:12px;color:var(--muted)}

/* hero */
.hero{position:absolute;left:0;top:56px;width:1089px;height:387px;background:var(--hero);overflow:hidden}
.hero-photo{position:absolute;left:420px;top:0;width:580px;height:387px;
  background:radial-gradient(ellipse at 30% 25%,#5a4436 0%,#2a1d16 30%,transparent 60%),
  radial-gradient(ellipse at 65% 55%,#7a5746 0%,#3b2a22 40%,#000 75%)}
.hero-kicker{position:absolute;left:148px;top:118px;font-size:17px;color:#fff}
.hero-title{position:absolute;left:147px;top:142px;font-size:25px;color:#fff;font-weight:400}
.hero-text{position:absolute;left:148px;top:183px;width:280px;font-size:12px;line-height:22px;color:#fff}
.hero-arrows{position:absolute;left:149px;top:285px;display:flex;gap:1px}
.hero-arrows span{width:24px;height:25px;background:#2a2a2a;display:flex;align-items:center;justify-content:center}

/* partners */
.partners-title{position:absolute;left:0;width:1089px;top:463px;text-align:center;font-size:19px;color:var(--ink)}
.partners-title small{font-size:12px}
.partner{position:absolute;top:523px;display:flex;align-items:center;gap:7px;font-size:17px;font-weight:700;color:#2d4f8a}
.partner i{display:block;width:22px;height:22px;border-radius:50%;background:#2d4f8a}
.chev{position:absolute;font-size:20px;color:#999}
.divider{position:absolute;left:0;top:571px;width:1089px;height:2px;background:var(--line)}

/* services */
.section-title{position:absolute;left:0;width:1089px;top:608px;text-align:center;font-size:20px;color:var(--brand)}
.section-sub{position:absolute;left:0;width:1089px;top:643px;text-align:center;font-size:14px;color:var(--ink)}
.section-intro{position:absolute;left:150px;width:789px;top:668px;text-align:center;font-size:10px;line-height:22px;color:var(--ink)}
.service{position:absolute;top:746px;width:260px}
.service-icon{position:absolute;left:0;top:0;width:51px;height:51px;border-radius:50%;background:var(--brand)}
.service h3{position:absolute;left:66px;top:5px;font-size:14px;font-weight:400;color:var(--brand)}
.service p{position:absolute;left:66px;top:30px;width:185px;font-size:8.5px;line-height:16px;color:var(--muted)}

/* news band */
.news-band{position:absolute;left:0;top:858px;width:1089px;height:256px;background:var(--light)}
.band-title{position:absolute;font-size:14px;color:var(--brand)}
.mini-arrows{position:absolute;font-size:11px;color:#777;letter-spacing:4px}
.news-photo{position:absolute;left:156px;top:929px;width:197px;height:140px;background:linear-gradient(135deg,#3a3e48,#a9a39c 55,#e8e6e2)}
.post-title{position:absolute;font-size:12px;line-height:18px;color:var(--brand)}
.post-text{position:absolute;font-size:8.5px;line-height:16px;color:var(--muted)}
.rule{position:absolute;left:631px;width:303px;height:1px;background:#d8d8d8}

/* footer */
.site-footer{position:absolute;left:0;top:1114px;width:1089px;height:86px;background:var(--footer)}
.footer-nav a{position:absolute;top:28px;font-size:8.5px;color:#ddd}
.copyright{position:absolute;left:158px;top:53px;font-size:8.5px;color:#ddd}
.social{position:absolute;top:31px;width:25px;height:25px;border-radius:50%;background:#6b6b6b}
</style>
</head>
<body>

<header class="site-header">
  <div class="brand"><span class="brand-mark"></span><span class="brand-name">plumbwick</span></div>
  <nav class="main-nav">
    <a style="left:414px">About us</a>
    <a style="left:507px">What we do</a>
    <a style="left:616px">News blog</a>
    <a style="left:717px">Articles</a>
    <a style="left:802px">Clients</a>
    <a style="left:885px">Partners</a>
  </nav>
</header>

<section class="hero">
  <div class="hero-photo" role="img" aria-label="Smiling woman holding a light bulb and an ideas folder"></div>
  <div class="hero-kicker">IT Support &amp;</div>
  <h1 class="hero-title">Management</h1>
  <p class="hero-text">Plumbwick was established with a specific aim: to consistently deliver an advanced and comprehen-sive IT service for ambitious growing companies across all industry sectors.</p>
  <div class="hero-arrows">
    <span><svg width="8" height="12"><path d="M6 1 1 6l5 5" stroke="#888" fill="none"/></svg></span>
    <span><svg width="8" height="12"><path d="M2 1l5 5-5 5" stroke="#888" fill="none"/></svg></span>
  </div>
</section>

<h2 class="partners-title">Partners : <small>Proud to be operating with the following industry leaders</small></h2>
<span class="chev" style="left:123px;top:521px">‹</span>
<div class="partner" style="left:160px"><i></i>CrateVault</div>
<div class="partner" style="left:357px">Arlo Studio</div>
<div class="partner" style="left:489px"><i></i>PostLantern</div>
<div class="partner" style="left:675px"><i></i>GateWarden</div>
<div class="partner" style="left:829px">KORVEX</div>
<span class="chev" style="left:948px;top:521px">›</span>
<div class="divider"></div>

<h2 class="section-title">Our products and services</h2>
<div class="section-sub">What we can do for you</div>
<p class="section-intro">Plumbwick offer a wide range of services tailored to meet our client's business needs. We aim to deliver world-class support and strategic advice backed-up by an effective on-site presence. Our core business is focussed on construction professionals and creative companies with sophisticated and fast-changing IT requirements.</p>

<span class="chev" style="left:114px;top:772px;font-size:24px">‹</span>
<div class="service" style="left:156px">
  <div class="service-icon"><svg width="51" height="51"><path d="M16 35 34 17M16 17l18 18" stroke="#fff" stroke-width="4" stroke-linecap="round"/></svg></div>
  <h3>Support</h3>
  <p>Plumbwick's clients enjoy regular scheduled on-site visits from an engineer. This provides a stable foundation for maintenance</p>
</div>
<div class="service" style="left:427px">
  <div class="service-icon"><svg width="51" height="51"><circle cx="18" cy="26" r="4" fill="#fff"/><circle cx="33" cy="26" r="4" fill="#fff"/><path d="M12 38a6 6 0 0 1 12 0zM27 38a6 6 0 0 1 12 0z" fill="#fff"/><circle cx="25.5" cy="15" r="3.5" fill="#fff"/></svg></div>
  <h3>Consultancy</h3>
  <p>Plumbwick's clients enjoy regular scheduled on-site visits from an engineer. This provides a stable foundation for maintenance</p>
</div>
<div class="service" style="left:693px">
  <div class="service-icon"><svg width="51" height="51"><circle cx="22" cy="29" r="6" fill="none" stroke="#fff" stroke-width="4"/><circle cx="32" cy="19" r="4" fill="none" stroke="#fff" stroke-width="3"/></svg></div>
  <h3>CAD</h3>
  <p>Plumbwick's clients enjoy regular scheduled on-site visits from an engineer. This provides a stable foundation for maintenance</p>
</div>
<span class="chev" style="left:969px;top:772px;font-size:24px">›</span>

<section class="news-band"></section>
<h2 class="band-title" style="left:156px;top:895px;font-weight:400">News blog</h2>
<span class="mini-arrows" style="left:561px;top:898px">‹ ›</span>
<div class="news-photo" role="img" aria-label="Business team discussing work around a laptop"></div>
<div class="post-title" style="left:373px;top:927px;width:200px">Plumbwick Pearphone and Droidly App launched</div>
<p class="post-text" style="left:373px;top:970px;width:210px">Plumbwick have released Pearphone and Droidly apps that allow customers to submit and track support requests on their smart phones.</p>
<p class="post-text" style="left:373px;top:1033px;width:215px">You can find the Pearphone version on TuneStore here and the Droidly version in the Droidly Market here</p>

<h2 class="band-title" style="left:631px;top:895px;font-weight:400">Articles latest</h2>
<span class="mini-arrows" style="left:910px;top:898px">‹ ›</span>
<div class="post-title" style="left:631px;top:927px">Plumbwick Pearphone and Droidly App launched</div>
<p class="post-text" style="left:631px;top:951px;width:300px">Plumbwick have released Pearphone and Droidly apps that allow customers to submit and track support requests on their smart phones.</p>
<div class="rule" style="top:995px"></div>
<div class="post-title" style="left:631px;top:1004px">Plumbwick Pearphone and Droidly App launched</div>
<p class="post-text" style="left:631px;top:1029px;width:300px">Plumbwick have released Pearphone and Droidly apps that allow customers to submit and track support requests on their smart phones.</p>
<div class="rule" style="top:1072px"></div>

<footer class="site-footer">
  <nav class="footer-nav">
    <a style="left:158px">Home</a>
    <a style="left:203px">About us</a>
    <a style="left:261px">What we do</a>
    <a style="left:330px">News blog</a>
    <a style="left:393px">Articles</a>
    <a style="left:444px">Clients</a>
    <a style="left:494px">Partners</a>
  </nav>
  <p class="copyright">Copyright © 2014. Plumb Wick. All rights reserved.</p>
  <span class="social" style="left:774px"></span>
  <span class="social" style="left:807px"></span>
  <span class="social" style="left:840px"></span>
  <span class="social" style="left:873px"></span>
  <span class="social" style="left:906px"></span>
</footer>

</body>
</html>
```